DJ Colm Vetter

I'm looking for a professional but still artsy/progressive design. I come from a hip hop/club DJ background playing a lot of underground music but have switched to doing more corporate parties and weddings recently. I am all about keeping the dancefloor moving and emotionally connecting with the crowd. I'd like a trendy/updated color palette. Something that's clean enough that looks professional but also trendy enough to convey that by the end of the night we'll be sweatily dancing to the latest hits. Some designers/artists I like: Tarn Olquist, Pavel Remy, Wendell Quarrie, Lumeno 7400, Silas Dravin.

```html
<!DOCTYPE html>
<html lang="en">
<head>
<meta charset="utf-8">
<title>DJ Colm Vetter — Business Card</title>
<link rel="stylesheet" href="https://fonts.googleapis.com/css2?family=Oswald:wght@500&family=Roboto:wght@300;400&display=swap">
<style>
  :root {
    --page-bg: #2a2420;
    --card-deep: #2b0f1e;
    --card-red: #a3213f;
    --card-magenta: #c2386a;
    --card-violet: #5a3470;
    --card-plum: #3a1c34;
    --text-light: #f4eef2;
    --text-soft: rgba(244, 238, 242, 0.85);
  }
  * { margin: 0; padding: 0; box-sizing: border-box; }
  html, body {
    width: 1200px; height: 1023px; overflow: hidden;
    background: var(--page-bg);
  }
  .stage {
    width: 1200px; height: 1023px;
    display: flex; align-items: center; justify-content: center;
  }
  .card {
    position: relative;
    width: 900px; height: 514px;
    border-radius: 26px;
    overflow: hidden;
    box-shadow: 0 24px 60px rgba(0, 0, 0, 0.5);
  }
  .card-photo {
    position: absolute; inset: 0;
    background:
      radial-gradient(ellipse at 22% 70%, var(--card-magenta) 0%, transparent 45%),
      radial-gradient(ellipse at 70% 30%, var(--card-violet) 0%, transparent 50%),
      radial-gradient(ellipse at 85% 80%, var(--card-red) 0%, transparent 40%),
      linear-gradient(135deg, var(--card-red) 0%, var(--card-plum) 55%, var(--card-deep) 100%);
  }
  .card-veil {
    position: absolute; inset: 0;
    background: linear-gradient(90deg, rgba(20, 6, 14, 0.15) 0%, rgba(20, 6, 14, 0.35) 100%);
  }
  .card-content {
    position: absolute;
    left: 170px; top: 250px;
    display: flex; align-items: center; gap: 28px;
    color: var(--text-light);
  }
  .identity { text-align: right; }
  .identity-name {
    font-family: "Oswald", sans-serif;
    font-weight: 500;
    font-size: 46px;
    line-height: 1;
    letter-spacing: 0.5px;
    text-transform: uppercase;
  }
  .identity-role {
    font-family: "Roboto", sans-serif;
    font-weight: 300;
    font-size: 20px;
    margin-top: 6px;
    color: var(--text-soft);
  }
  .divider {
    width: 1.5px; height: 90px;
    background: var(--text-soft);
  }
  .contact {
    list-style: none;
    font-family: "Roboto", sans-serif;
    font-weight: 300;
    font-size: 21px;
    line-height: 1.45;
  }
  .contact li { display: flex; align-items: center; gap: 10px; }
  .contact svg { width: 14px; height: 14px; fill: none; stroke: var(--text-light); stroke-width: 1.6; }
</style>
</head>
<body>
  <main class="stage">
    <section class="card">
      <div class="card-photo" role="img" aria-label="Blurred close-up photo of a DJ's hands on a mixing console under red and purple club lights"></div>
      <div class="card-veil"></div>
      <div class="card-content">
        <div class="identity">
          <h1 class="identity-name">DJ Colm Vetter</h1>
          <p class="identity-role">Director</p>
        </div>
        <div class="divider"></div>
        <ul class="contact">
          <li>
            <svg viewBox="0 0 16 16"><path d="M4 2l2 3-1.5 1.5a8 8 0 0 0 5 5L11 10l3 2-1 2.5C7 14 2 9 1.5 3z"/></svg>
            +330 5120-4417
          </li>
          <li>
            <svg viewBox="0 0 16 16"><rect x="1.5" y="3.5" width="13" height="9"/><path d="M1.5 3.5l6.5 5 6.5-5"/></svg>
            hello@colmvetter.com
          </li>
          <li>
            <svg viewBox="0 0 16 16"><circle cx="8" cy="8" r="6.5"/><path d="M1.5 8h13M8 1.5c3 3.5 3 9.5 0 13M8 1.5c-3 3.5-3 9.5 0 13"/></svg>
            www.colmvetter.com
          </li>
        </ul>
      </div>
    </section>
  </main>
</body>
</html>
```